Will you marry me post card

I am just looking for a postcard to send my partner that will ask him to marry me.
I plan on creating about 200 of them and mailing them all at once so that he gets them all on the same day.
They should all be similar or could have a few different options.
I would like it simple, elegant, clean and crisp. No images, just text or icons

My only requirement is the text, "will you marry me?" in all lowercase -- any fonts, can be big, small, varying sizes, repeated, whole card, tiny space, don't care...just amazing design. BUT SIMPLE!

```html
<!DOCTYPE html>
<html lang="en">
<head>
<meta charset="utf-8">
<title>will you marry me? — postcard</title>
<link rel="stylesheet" href="https://fonts.googleapis.com/css2?family=Stint+Ultra+Condensed&display=swap">
<style>
  :root {
    --backdrop: #ece7e9;
    --crimson: #96234b;
    --accent: #8f1f48;
    --ink-light: #ffffff;
    --blush-top: #d8cad3;
    --blush-mid: #f6bcc8;
    --blush-low: #b3b7cb;
  }
  * { margin: 0; padding: 0; box-sizing: border-box; }
  html, body {
    width: 1200px;
    height: 821px;
    overflow: hidden;
    background: var(--backdrop);
  }
  .postcard {
    position: absolute;
    left: 140px;
    top: 111px;
    width: 921px;
    height: 599px;
    display: flex;
  }
  .postcard__front {
    position: relative;
    width: 460px;
    height: 100%;
    overflow: hidden;
    background:
      radial-gradient(ellipse 70% 45% at 70% 45%, var(--blush-mid) 0%, rgba(246,188,200,0) 100%),
      radial-gradient(ellipse 60% 35% at 85% 95%, var(--blush-low) 0%, rgba(179,183,203,0) 100%),
      linear-gradient(170deg, var(--blush-top) 0%, #e9c3cf 50%, #c9bccd 100%);
  }
  .postcard__back {
    width: 461px;
    height: 100%;
    background: var(--crimson);
  }
  .proposal {
    position: absolute;
    inset: 0;
    width: 460px;
    height: 599px;
  }
  .proposal__line {
    font-family: "Stint Ultra Condensed", "Arial Narrow", serif;
    font-size: 190px;
    fill: var(--ink-light);
  }
  .proposal__accent { fill: var(--accent); }
  .proposal__heart {
    fill: none;
    stroke: var(--accent);
    stroke-width: 5;
    stroke-linejoin: round;
  }
</style>
</head>
<body>
  <main class="postcard">
    <section class="postcard__front">
      <svg class="proposal" viewBox="0 0 460 599" role="img" aria-label="will you marry me?">
        <text class="proposal__line" x="53" y="184" textLength="155" lengthAdjust="spacingAndGlyphs">w<tspan class="proposal__accent">i</tspan>ll</text>
        <text class="proposal__line" x="63" y="299" textLength="52" lengthAdjust="spacingAndGlyphs">y</text>
        <path class="proposal__heart" d="M140 287 C132 262 117 242 117 216 C117 203 123 195 131 195 C136 195 139 199 140 207 C141 199 144 195 149 195 C157 195 163 203 163 216 C163 242 148 262 140 287 Z"/>
        <text class="proposal__line proposal__accent" x="166" y="299" textLength="52" lengthAdjust="spacingAndGlyphs">u</text>
        <text class="proposal__line" x="108" y="414" textLength="305" lengthAdjust="spacingAndGlyphs">marry</text>
        <text class="proposal__line" x="125" y="529" textLength="190" lengthAdjust="spacingAndGlyphs">me?</text>
      </svg>
    </section>
    <section class="postcard__back" aria-label="card back"></section>
  </main>
</body>
</html>
```